Web Infographic for Life Insurance

We need an infographic for our insurance site based on research commissioned previously. We have a report of statistics on the cost and coverage of life insurance in 1999 vs 2019. What we're looking for is an infographic that presents these statistics in an entertaining and informative way. Site is CoverWren.com
Target Market(s)
Americans ages 30-65 interested in life insurance.
Industry/Entity Type
Insurance
Number of Pages Required
1 page
Font styles to use
Sans Serif
Decorative
Colors
85cae6
faa54b
ffffff
86cfc6
Requirements
Must have
- Long vertical infographic readable on mobile devices
Nice to have
- Footnote references
Should not have
- Extremely small text
- Any brand logos or trademarked imagery other than for coverwren

```html
<!DOCTYPE html>
<html lang="en">
<head>
<meta charset="utf-8">
<title>CoverWren – The Cost and Coverage of Life Insurance in 1999 vs 2019</title>
<link href="https://fonts.googleapis.com/css2?family=Poppins:ital,wght@0,300;0,400;0,500;0,600;0,700;1,300&display=swap" rel="stylesheet">
<style>
  :root{
    --orange:#f7953b;
    --orange-light:#f8b878;
    --orange-dark:#d35f14;
    --tan:#e49a5b;
    --amber:#da8a3b;
    --teal:#75c7bb;
    --teal-mid:#36b09e;
    --teal-dark:#1d7f6d;
    --teal-soft:#4aa391;
    --mint:#5ff1d6;
    --mint-2:#4de0c9;
    --sky:#85cae6;
    --blue:#2a86c9;
    --ink:#111111;
    --grey:#444;
    --white:#ffffff;
    --red-cap:#e5332a;
    --green-cap:#37d63a;
  }
  *{margin:0;padding:0;box-sizing:border-box}
  html,body{width:1200px;height:5249px;overflow:hidden;background:var(--white)}
  body{position:relative;font-family:"Poppins",sans-serif;color:var(--ink)}
  .abs{position:absolute}
  .art{position:absolute}
  .bg-svg{position:absolute;left:0;top:0}

  /* header */
  .brand{left:110px;top:28px;font-size:46px;font-weight:600;letter-spacing:-1px}
  .contact{right:60px;top:30px;font-size:19px;font-weight:600;display:flex;align-items:center;gap:8px}
  .main-title{left:110px;top:246px;font-size:38px;font-weight:700;line-height:54px;width:700px}

  .section-title{left:0;width:1200px;text-align:center;font-size:34px;font-weight:700;line-height:40px}

  /* summary */
  .bubble{left:102px;top:905px;width:175px;height:135px;background:var(--orange);border-radius:26px;text-align:center;font-size:12px;font-weight:600;padding-top:26px;line-height:25px}
  .bubble b{font-size:18px;display:block}
  .arrow-label{top:1108px;font-size:16px;font-weight:600}
  .legend-dot{font-size:15px;font-weight:600;display:flex;align-items:center;gap:14px}
  .legend-dot i{width:12px;height:12px;border-radius:50%;background:var(--orange);display:inline-block}
  .real-amount{left:860px;width:340px;top:1165px;text-align:center;font-size:16px;font-weight:600;line-height:25px}

  .caption{font-size:15.5px;font-style:italic;font-weight:300;text-align:center;line-height:26px}

  /* numbers section */
  .numbers{left:0;top:1960px;width:1200px;height:947px;background:var(--orange);overflow:hidden}
  .numbers .section-title{color:var(--white);top:106px}
  .stat-circle{position:absolute;border-radius:50%;display:flex;align-items:center;justify-content:center;color:var(--white);font-weight:700;font-size:24px}
  .numbers .stat-circle{background:#9ed8cd;width:86px;height:86px}
  .stat-text{position:absolute;color:var(--white);font-size:16.5px;font-weight:400;line-height:26px;padding-bottom:2px;border-bottom:2px solid rgba(255,255,255,.75)}

  /* cost section */
  .cost{left:0;top:2907px;width:1200px;height:1025px;background:var(--teal);overflow:hidden}
  .cost .section-title{color:var(--white);top:96px}
  .cost .stat-circle{background:var(--orange);width:80px;height:80px;font-size:24px}
  .cost .stat-text{text-align:right}

  /* chart */
  .axis-num{font-size:15px;font-weight:700;left:68px}
  .bar{position:absolute;width:45px}
  .bar-val{position:absolute;width:70px;text-align:center;font-size:15px;color:var(--grey)}
  .key{position:absolute;display:flex;align-items:center;gap:22px;font-size:15.5px;font-weight:500;color:var(--grey)}
  .key i{display:block;width:33px;height:33px}

  .footer{top:5162px;left:0;width:1200px;text-align:center;font-size:15px;color:var(--grey)}
  .page-no{top:5162px;right:55px;font-size:15px;color:var(--grey)}
</style>
</head>
<body>

<!-- header -->
<svg class="bg-svg" width="1200" height="760" viewBox="0 0 1200 760" aria-hidden="true">
  <path d="M780 0 H1200 V520 L950 712 Q870 770 790 708 L470 470 Q410 420 470 370 Z" fill="var(--orange)"/>
</svg>
<div class="brand abs">coverwren</div>
<div class="contact abs">
  <svg width="20" height="15" viewBox="0 0 20 15" aria-hidden="true"><rect x="0" y="0" width="20" height="15" rx="2" fill="#111"/><path d="M1 1 L10 8 L19 1" stroke="#fff" stroke-width="2" fill="none"/></svg>
  Help@CoverWren.com
</div>
<h1 class="main-title abs">THE COST AND COVERAGE OF LIFE INSURANCE IN 1999 VS 2019</h1>
<div class="art" role="img" aria-label="Illustration of a blue umbrella sheltering a red heart over an insurance policy document with a family and a pen" style="left:690px;top:165px;width:470px;height:390px;border-radius:40px;background:radial-gradient(circle at 50% 40%, #e8483c 0 18%, #2a86c9 19% 40%, #e9e9ef 41% 60%, transparent 61%)"></div>

<!-- summary statistics -->
<h2 class="section-title abs" style="top:832px">SUMMARY STATISTICS<br>1992–1997</h2>
<div class="art" role="img" aria-label="Illustration of a businessman in a suit talking on the phone, holding a briefcase" style="left:0;top:960px;width:250px;height:300px;background:linear-gradient(180deg,#f4f4f6,#e6e6ec);border-radius:0 120px 120px 0"></div>
<div class="bubble abs">TYPE TERM PREMIUM/<br>($1000 OF FACE)<b>3.62</b></div>
<svg class="bg-svg" width="1200" height="1300" viewBox="0 0 1200 1300" aria-hidden="true">
  <path d="M190 1038 L230 1040 L200 1070 Z" fill="var(--orange)"/>
  <path d="M373 1095 H636 V1055 L774 1118 L636 1182 V1142 H373 Z" fill="var(--orange)"/>
</svg>
<div class="arrow-label abs" style="left:428px">LENGTH OF POLICY</div>
<div class="arrow-label abs" style="left:668px;font-size:19px;top:1104px">2.27</div>
<div class="legend-dot abs" style="left:434px;top:1192px"><i></i>NON-SMOKER</div>
<div class="legend-dot abs" style="left:434px;top:1218px"><i></i>MALE</div>
<div class="art" role="img" aria-label="Illustration of hands signing an insurance policy on a clipboard" style="left:835px;top:940px;width:365px;height:220px;background:linear-gradient(135deg,#f2f2f4 0%,#dfe6ee 60%,#f4b88a 100%);border-radius:12px"></div>
<div class="real-amount abs">REAL AMOUNT OF POLICY<br>(IN '000S OF 1990 DOLLARS)<br>132.97 (136.41)</div>

<!-- policy purchases -->
<h2 class="section-title abs" style="top:1356px">NUMBER OF LIFE INSURANCE POLICY<br>PURCHASES IN THE UNITED STATES<br>FROM 1998 TO 2018</h2>
<div class="art" role="img" aria-label="Illustration of a large crowd of colourful people" style="left:0;top:1532px;width:330px;height:262px;background:linear-gradient(135deg,#e3f2f6,#f7d9c4,#c9e4f3)"></div>
<div class="art" role="img" aria-label="Coloured map of the United States" style="left:401px;top:1565px;width:404px;height:228px;background:linear-gradient(135deg,#f1ead2,#d9c89b,#b9c9a0)"></div>
<div class="art" role="img" aria-label="Illustration of a man watching a rising blue arrow" style="left:950px;top:1530px;width:228px;height:228px;border-radius:50%;background:radial-gradient(circle at 40% 35%,#3aa0e0,#1b6fb0)"></div>
<svg class="bg-svg" width="1200" height="1800" viewBox="0 0 1200 1800" aria-hidden="true">
  <path d="M305 1672 Q360 1690 392 1660" stroke="var(--orange)" stroke-width="6" fill="none"/>
  <path d="M380 1650 L400 1655 L392 1676 Z" fill="var(--orange)"/>
  <path d="M805 1685 Q860 1700 886 1665" stroke="var(--orange)" stroke-width="6" fill="none"/>
  <path d="M874 1656 L896 1660 L886 1682 Z" fill="var(--orange)"/>
</svg>
<p class="caption abs" style="left:440px;width:330px;top:1802px;color:var(--red-cap)">growth of the Internet has reduced<br>term life prices by 8–15 percent</p>
<p class="caption abs" style="left:850px;width:350px;top:1806px;color:var(--green-cap)">approximately 27.8 million life insurance<br>policies were purchased in the United States</p>

<!-- life insurance by the numbers -->
<section class="numbers abs">
  <svg class="bg-svg" width="1200" height="947" viewBox="0 0 1200 947" aria-hidden="true">
    <path d="M0 220 Q300 150 400 430 Q460 680 180 860 L0 947 Z" fill="#6ec4bb"/>
    <path d="M200 120 Q470 300 440 520 Q410 700 280 830" stroke="#9ed8cd" stroke-width="5" fill="none"/>
  </svg>
  <div class="art" role="img" aria-label="Illustration of a smiling family sheltering under a green umbrella" style="left:0;top:300px;width:320px;height:420px;border-radius:0 160px 160px 0;background:linear-gradient(180deg,#7ccf3c 0 28%,#f2b48a 28% 60%,#4f86c6 60%)"></div>
  <h2 class="section-title abs">LIFE INSURANCE BY THE NUMBERS</h2>

  <div class="stat-circle" style="left:232px;top:191px">57%</div>
  <p class="stat-text" style="left:369px;top:214px;width:540px">Percent of American adults who have life insurance</p>

  <div class="stat-circle" style="left:334px;top:289px">32%</div>
  <p class="stat-text" style="left:442px;top:285px;width:565px">Of American adults with life insurance, the percent who only have group coverage — which usually isn't enough (and is rarely portable)</p>

  <div class="stat-circle" style="left:383px;top:417px">12%</div>
  <p class="stat-text" style="left:487px;top:410px;width:640px">The multiples of your annual income that most financial advisors recommend you need when buying life insurance for income replacement</p>

  <div class="stat-circle" style="left:381px;top:560px">50%</div>
  <p class="stat-text" style="left:487px;top:576px;width:570px">Percent of life insurance policies are purchased via independent agents</p>

  <div class="stat-circle" style="left:309px;top:692px">40%</div>
  <p class="stat-text" style="left:463px;top:680px;width:650px">Percent of life insurance policies purchased via affiliated agents (meaning they only sell products for one insurance company)</p>
</section>

<!-- stats about cost -->
<section class="cost abs">
  <svg class="bg-svg" width="1200" height="1025" viewBox="0 0 1200 1025" aria-hidden="true">
    <circle cx="1120" cy="620" r="345" fill="var(--orange)"/>
    <path d="M980 160 Q760 260 700 430 Q660 600 760 740 Q830 820 900 843" stroke="var(--orange)" stroke-width="5" fill="none"/>
  </svg>
  <div class="art" role="img" aria-label="Illustration of a person on a ladder under an umbrella beside a large red heart, with a doctor carrying a medical kit" style="left:850px;top:330px;width:350px;height:560px;border-radius:40px 0 0 40px;background:radial-gradient(circle at 60% 45%,#e7463b 0 30%,#f38c5b 31% 55%,transparent 56%)"></div>
  <h2 class="section-title abs">STATS ABOUT THE COST OF LIFE INSURANCE</h2>

  <p class="stat-text" style="left:235px;top:157px;width:600px">How much more permanent life insurance (like whole<br>life insurance) costs vs. term life insurance</p>
  <div class="stat-circle" style="left:852px;top:164px">10%</div>

  <p class="stat-text" style="left:145px;top:294px;width:575px">Average percent increase in your insurance costs as<br>you age, assuming your health stays the same</p>
  <div class="stat-circle" style="left:738px;top:268px">8%</div>

  <p class="stat-text" style="left:40px;top:425px;width:600px">The average cost difference between sequential<br>health ratings (preferred vs standard, for example)</p>
  <div class="stat-circle" style="left:651px;top:416px">30%</div>

  <p class="stat-text" style="left:0;top:577px;width:650px">How much rates for smokers cost vs. rates for nonsmokers (but a year<br>after you quit smoking, most companies will offer you nonsmoker rates)</p>
  <div class="stat-circle" style="left:657px;top:577px">2.5%</div>

  <p class="stat-text" style="left:60px;top:711px;width:645px">The average difference between the least expensive and most expensive<br>rate for the same person across insurance companies</p>
  <div class="stat-circle" style="left:724px;top:700px">50%</div>

  <p class="stat-text" style="left:230px;top:814px;width:600px">Percent difference between premiums for men and women<br>(with women paying nearly ⅓ less than men, on average)</p>
  <div class="stat-circle" style="left:848px;top:803px">30%</div>
</section>

<!-- top reasons chart -->
<h2 class="section-title abs" style="top:4050px">TOP REASONS FOR BUYING LIFE<br>INSURANCE IN THE U.S.</h2>
<svg class="bg-svg" width="1200" height="4760" viewBox="0 0 1200 4760" aria-hidden="true">
  <g stroke="#444" stroke-width="1.5">
    <line x1="96" y1="4213" x2="1155" y2="4213"/>
    <line x1="96" y1="4321" x2="1155" y2="4321"/>
    <line x1="96" y1="4427" x2="1155" y2="4427"/>
    <line x1="96" y1="4535" x2="1155" y2="4535"/>
    <line x1="96" y1="4641" x2="1155" y2="4641"/>
  </g>
  <line x1="96" y1="4135" x2="96" y2="4716" stroke="#111" stroke-width="2"/>
  <line x1="80" y1="4692" x2="1155" y2="4692" stroke="#111" stroke-width="2"/>
</svg>
<span class="axis-num abs" style="top:4196px">50</span>
<span class="axis-num abs" style="top:4304px">40</span>
<span class="axis-num abs" style="top:4410px">30</span>
<span class="axis-num abs" style="top:4518px">20</span>
<span class="axis-num abs" style="top:4624px">10</span>

<div class="bar" style="left:149px;top:4352px;height:340px;background:var(--orange)"></div><span class="bar-val" style="left:136px;top:4326px">37%</span>
<div class="bar" style="left:241px;top:4427px;height:265px;background:var(--teal)"></div><span class="bar-val" style="left:228px;top:4401px">30%</span>
<div class="bar" style="left:333px;top:4449px;height:243px;background:var(--orange-light)"></div><span class="bar-val" style="left:320px;top:4423px">28%</span>
<div class="bar" style="left:425px;top:4470px;height:222px;background:var(--teal-dark)"></div><span class="bar-val" style="left:412px;top:4444px">27%</span>
<div class="bar" style="left:517px;top:4545px;height:147px;background:var(--orange-dark)"></div><span class="bar-val" style="left:504px;top:4519px">19%</span>
<div class="bar" style="left:609px;top:4567px;height:125px;background:var(--mint)"></div><span class="bar-val" style="left:596px;top:4541px">17%</span>
<div class="bar" style="left:701px;top:4598px;height:94px;background:var(--tan)"></div><span class="bar-val" style="left:688px;top:4572px">14%</span>
<div class="bar" style="left:793px;top:4598px;height:94px;background:var(--teal-mid)"></div><span class="bar-val" style="left:780px;top:4572px">14%</span>
<div class="bar" style="left:885px;top:4609px;height:83px;background:var(--amber)"></div><span class="bar-val" style="left:872px;top:4583px">13%</span>
<div class="bar" style="left:977px;top:4662px;height:30px;background:var(--mint-2)"></div><span class="bar-val" style="left:964px;top:4636px">8%</span>
<div class="bar" style="left:1069px;top:4662px;height:30px;background:var(--teal-soft)"></div><span class="bar-val" style="left:1056px;top:4636px">8%</span>

<div class="key" style="left:180px;top:4756px"><i style="background:var(--orange)"></i>37% INCOME REPLACEMENT</div>
<div class="key" style="left:180px;top:4821px"><i style="background:var(--teal)"></i>30% BURIAL/FINAL EXPENSES</div>
<div class="key" style="left:180px;top:4886px"><i style="background:var(--orange-light)"></i>28% WEALTH TRANSFER</div>
<div class="key" style="left:180px;top:4952px"><i style="background:var(--teal-dark)"></i>27% PAY OFF MORTGAGE</div>
<div class="key" style="left:180px;top:5017px"><i style="background:var(--orange-dark)"></i>19% REPLACED A POLICY</div>
<div class="key" style="left:180px;top:5082px"><i style="background:var(--mint)"></i>17% TAX ADVANTAGED SAVE/INVEST</div>
<div class="key" style="left:640px;top:4756px"><i style="background:var(--tan)"></i>14% ESTATE TAXES/LIQUIDITY</div>
<div class="key" style="left:640px;top:4821px"><i style="background:var(--teal-mid)"></i>14% FUNDS FOR COLLEGE EDUCATION</div>
<div class="key" style="left:640px;top:4886px"><i style="background:var(--amber)"></i>13% CHARITABLE GIFT</div>
<div class="key" style="left:640px;top:4952px"><i style="background:var(--mint-2)"></i>8% SUPPLEMENT GROUP COVERAGE</div>
<div class="key" style="left:640px;top:5017px"><i style="background:var(--teal-soft)"></i>8% BUSINESS PURPOSES</div>

<footer class="footer abs">© Copy Rights Cover Wren &nbsp;&nbsp;|&nbsp;&nbsp; All Rights Reserved</footer>
<span class="page-no abs">C 43</span>

</body>
</html>
```